Modern Business Card

Modern professional business card with more than just logo and demographic info. Something memorable.

We are a trendy/modern chiropractic group with an emphasis on neurology, hence the minimalist-type brain logo. We want to convey that modern and technical aspect with professionalism and the elite nature of our practice environment.

```html
<!DOCTYPE html>
<html lang="en">
<head>
<meta charset="utf-8">
<title>Keystone Chiropractic – Business Card</title>
<link rel="stylesheet" href="https://fonts.googleapis.com/css2?family=Lora:wght@400;700&family=Montserrat:wght@400&display=swap">
<style>
  :root {
    --brand-blue: #4a80c2;
    --ring-grey: #47484c;
    --paper: #ffffff;
    --ink: #222326;
    --backdrop: #d9dadc;
    --serif: "Lora", Georgia, serif;
    --sans: "Montserrat", Arial, sans-serif;
  }
  * { box-sizing: border-box; margin: 0; padding: 0; }
  html, body { width: 1200px; height: 901px; overflow: hidden; }
  body {
    background: var(--backdrop);
    display: flex;
    align-items: center;
    justify-content: center;
    gap: 40px;
  }
  .card {
    position: relative;
    width: 540px;
    height: 309px;
    overflow: hidden;
    box-shadow: 0 6px 18px rgba(0,0,0,.25);
  }
  .card--front {
    background: var(--brand-blue);
    display: flex;
    align-items: center;
    justify-content: center;
  }
  .wordmark {
    font-family: var(--serif);
    font-weight: 400;
    text-transform: uppercase;
    line-height: 1;
  }
  .wordmark__primary { display: block; letter-spacing: 2px; }
  .wordmark__secondary { display: block; letter-spacing: 1.5px; }
  .card--front .wordmark { color: var(--paper); }
  .card--front .wordmark__primary { font-size: 46px; }
  .card--front .wordmark__secondary { font-size: 25px; margin-top: 4px; }

  .card--back { background: var(--brand-blue); }
  .card__curve { position: absolute; inset: 0; }
  .card--back .wordmark {
    position: absolute;
    left: 318px;
    top: 92px;
    color: var(--ink);
  }
  .card--back .wordmark__primary { font-size: 27px; }
  .card--back .wordmark__secondary { font-size: 14.5px; margin-top: 3px; }

  .details {
    position: absolute;
    left: 36px;
    top: 104px;
    color: var(--paper);
    font-family: var(--sans);
  }
  .details__name {
    font-family: var(--serif);
    font-weight: 700;
    font-size: 19px;
    letter-spacing: .5px;
    text-transform: uppercase;
  }
  .details__role { font-size: 12.5px; margin-top: 2px; margin-left: 10px; }
  .details__address { font-size: 12.5px; line-height: 1.35; margin-top: 26px; margin-left: 24px; }
  .contact-list { list-style: none; margin-top: 24px; margin-left: 34px; }
  .contact-list li {
    display: flex;
    align-items: center;
    gap: 7px;
    font-size: 12px;
    line-height: 1.5;
  }
  .contact-list svg { width: 10px; height: 10px; fill: var(--paper); flex: none; }
</style>
</head>
<body>
  <section class="card card--front" aria-label="Card front">
    <div class="wordmark">
      <span class="wordmark__primary">Keystone</span>
      <span class="wordmark__secondary">Chiropractic</span>
    </div>
  </section>

  <section class="card card--back" aria-label="Card back">
    <svg class="card__curve" viewBox="0 0 540 309" aria-hidden="true">
      <circle cx="560" cy="-40" r="355" fill="var(--ring-grey)"/>
      <circle cx="572" cy="-52" r="350" fill="var(--paper)"/>
    </svg>
    <div class="wordmark">
      <span class="wordmark__primary">Keystone</span>
      <span class="wordmark__secondary">Chiropractic</span>
    </div>
    <div class="details">
      <p class="details__name">Daniel Marsh</p>
      <p class="details__role">Senior Partner</p>
      <p class="details__address">12 Fernhill Road Northcliff<br>Pretoria, 0182</p>
      <ul class="contact-list">
        <li><svg viewBox="0 0 10 10"><path d="M2 0.5 L3.6 2.6 L2.8 3.6 Q4 6 6.4 7.2 L7.4 6.4 L9.5 8 L8.4 9.5 Q3 9 0.5 1.6 Z"/></svg>+120 5000 1234</li>
        <li><svg viewBox="0 0 10 10"><path d="M2.5 0 H7.5 V10 H2.5 Z M3.3 1 V8 H6.7 V1 Z"/></svg>+965 8000 5678</li>
        <li><svg viewBox="0 0 10 10"><path d="M0 2 H10 V8.5 H0 Z M0.8 2.6 L5 5.6 L9.2 2.6 Z"/></svg>info@keystonechiro.com</li>
        <li><svg viewBox="0 0 10 10"><path d="M5 0 A5 5 0 1 0 5.01 0 Z M5 1 A4 4 0 0 1 5 9 A4 4 0 0 1 5 1 Z M1 4.6 H9 V5.4 H1 Z M4.6 1 H5.4 V9 H4.6 Z"/></svg>www.keystonechiro.com</li>
      </ul>
    </div>
  </section>
</body>
</html>
```